Media Services Start-up -- Corporate Website and Logo Design. Inspiration required!

We need a logo design and corporate website design, including coding, for our start-up business.
Vennatra’s value proposition is based on bringing together media content from a vast number of geographies globally, adding human and AI curation, translation and editing, and delivering the content using tailored customer interfaces. On the one hand, the business brings together media coverage from all over the world, and on the other it brings together content, human skills and technology to deliver a supreme customer experience.
Vennatra is a B2B media monitoring and analytics business with emphasis on global customers. Vennatra's service offering is centred around sourcing media content from different markets, processing, storing and delivering the content and insights derived from it using an online platform / mobile app.
The messaging we want to create through the logo is:
- Global scope
- Speed of delivery
- Cost-efficiency
- Multi-lingual
- Tailor-made
- Trustworthy
Target Market(s)
Business to business, PR / Communications, Media, Marketing
Logo Text
Vennatra
Coding
Coded - Design and coding required
Number of Pages Required
5+ page
Font styles to use
Other font styles liked:
- See Design Brief for details
Colors
Designer to choose colors to be used in the design.

```html
<!DOCTYPE html>
<html lang="en">
<head>
<meta charset="utf-8">
<title>Vennatra — Global Media Intelligence</title>
<link href="https://fonts.googleapis.com/css2?family=Roboto:wght@400;500;700&display=swap" rel="stylesheet">
<style>
  :root {
    --ink: #000000;
    --paper: #ffffff;
    --hero-dark: #0d1419;
    --hero-mid: #1c2f3d;
    --hero-glow: #2f5269;
    --field-border: #555555;
    --placeholder: #6b6b6b;
  }
  * { box-sizing: border-box; margin: 0; padding: 0; }
  html, body { width: 1200px; height: 747px; overflow: hidden; background: var(--paper); }
  body { position: relative; font-family: "Roboto", Arial, sans-serif; color: var(--ink); }

  .site-header { position: absolute; left: 0; top: 0; width: 1200px; height: 71px; background: var(--paper); }
  .brand { position: absolute; left: 143px; top: 15px; font-size: 29px; font-weight: 700; letter-spacing: 0.2px; }
  .main-nav a { position: absolute; top: 26px; font-size: 14px; color: var(--ink); text-decoration: none; }
  .sign-in {
    position: absolute; left: 967px; top: 18px; width: 92px; height: 35px;
    background: var(--ink); color: var(--paper); border-radius: 3px;
    font-size: 15px; line-height: 35px; text-align: center;
    box-shadow: 0 3px 8px rgba(0,0,0,0.25);
  }

  .hero { position: absolute; left: 0; top: 71px; width: 1200px; height: 634px; overflow: hidden; }
  .hero-backdrop {
    position: absolute; inset: 0;
    background:
      radial-gradient(ellipse 380px 260px at 560px 230px, var(--hero-glow) 0%, transparent 70%),
      radial-gradient(ellipse 520px 200px at 620px 560px, #27465a 0%, transparent 75%),
      linear-gradient(180deg, var(--hero-dark) 0%, var(--hero-mid) 55%, #12202a 100%);
  }
  .hero-title {
    position: absolute; left: 140px; top: 192px; width: 580px;
    color: var(--paper); font-size: 37.5px; font-weight: 700; line-height: 58px; letter-spacing: 0.5px;
  }
  .hero-intro {
    position: absolute; left: 142px; top: 328px; width: 445px;
    color: var(--paper); font-family: Arial, "Roboto", sans-serif; font-size: 16.5px; line-height: 25.4px;
  }

  .lead-card {
    position: absolute; left: 766px; top: 155px; width: 293px; height: 322px;
    background: var(--paper); border-radius: 5px; padding: 4px;
    box-shadow: 0 2px 8px rgba(0,0,0,0.3);
  }
  .lead-card h2 {
    height: 49px; background: var(--ink); color: var(--paper);
    font-size: 17px; font-weight: 500; line-height: 49px; text-align: center;
  }
  .field {
    position: absolute; left: 32px; width: 228px; height: 37px;
    border: 1px solid var(--field-border); border-radius: 3px;
    padding-left: 13px; font-size: 13px; line-height: 35px; color: var(--placeholder);
  }
  .get-started {
    position: absolute; left: 58px; top: 255px; width: 177px; height: 35px;
    background: var(--ink); color: var(--paper); border-radius: 2px;
    font-size: 15px; line-height: 35px; text-align: center; letter-spacing: 0.3px;
  }

  .site-footer { position: absolute; left: 0; top: 705px; width: 1200px; height: 42px; background: var(--paper); }
  .copyright { position: absolute; left: 143px; top: 13px; font-size: 12.5px; }
  .social { position: absolute; left: 951px; top: 10px; }
</style>
</head>
<body>
  <header class="site-header">
    <div class="brand">Vennatra</div>
    <nav class="main-nav">
      <a style="left:363px">Home</a>
      <a style="left:455px">Solutions</a>
      <a style="left:568px">How We Do It</a>
      <a style="left:707px">Our People</a>
      <a style="left:829px">Our Technology</a>
    </nav>
    <div class="sign-in">SIGN IN</div>
  </header>

  <section class="hero">
    <div class="hero-backdrop" role="img" aria-label="Photo of a businessman holding a tablet with a glowing globe and social network icons"></div>
    <h1 class="hero-title">DELIVERING GLOBAL MEDIA INTELLIGENCE</h1>
    <p class="hero-intro">Vennatra is an international media intelligence service provider. We help communications teams builds and operate truly global media monitoring and measurement programmes.</p>

    <form class="lead-card">
      <h2>Learn More About Vennatra</h2>
      <div class="field" style="top:81px">Name</div>
      <div class="field" style="top:138px">Email Address</div>
      <div class="field" style="top:194px">Phone</div>
      <div class="get-started">GET STARTED</div>
    </form>
  </section>

  <footer class="site-footer">
    <div class="copyright">© 2019 Vennatra Analytics Media. All rights reserved.</div>
    <svg class="social" width="110" height="24" viewBox="0 0 110 24" role="img" aria-label="Social network links">
      <circle cx="11" cy="12" r="11" fill="#000"/>
      <circle cx="39.5" cy="12" r="11" fill="#000"/>
      <circle cx="68" cy="12" r="11" fill="#000"/>
      <circle cx="96.5" cy="12" r="11" fill="#000"/>
    </svg>
  </footer>
</body>
</html>
```